Web Design Project

Website Design Brief

Company Details
1a) Name of Company

MAPLEHAVEN
1) What is the nature of your business?: Briefly describe your products or services:

INDEPENDENT CONTEMPORARY TRADITIONAL ITALIAN RESTAURANT IN THE HEART OF ELMSWORTH QUAY ALSO CATERING FOR PRIVATE CORPORATE EVENTS AND WEDDING RECEPTIONS

1a) Who is your target market? Who are you hoping to reach with your site?

CITY CORPORATES, LOCAL CORPORATES/BUSINESSES, LOCAL RESIDENTS, VISITORS TO THE DOCK, LOCAL HOTELS

Website Details
1b) Do you have an existing website? If so, what is the URL?
HTTP://WWW.MAPLEHAVENTRATTORIA.EXAMPLE

2b) IMPORTANT: Please list at least 3 URLs (web addresses) of high quality sites that you like the look of (these do not have to be sites who’s business is similar to yours. It aids us in determining what your design style is.) Please consider layout, colours, navigation, graphics, and typography.

http://www.thecorvelle.example/

http://www.dunmorrow.example/

http://www.pavokitchen.example/

http://www.ilfaro.example/

3b) What colours or colour schemes would you like?

WHITE, BLACK, SILVER/ALUMINIUM (PLS LOOK AT OUR OUTSIDE CHAIRS)

4b) List the Navigation links for your Site:

5b) What type of look are you trying to achieve? (e.g. clean, high-tech, conservative, warm, flashy, etc.)

SIMPLE ELEGANT CLASSY INFORMATIVE, EASY TO USE, A REFLECTION OF THE BUSINESS ITSELF

6b) Please provide the addresses of competitors' sites, if possible:

Do not contact the client direct - all questions should go through Brightwell Venues - info@brightwellvenues.example
Updates

thanks for the designs that I have received so far. I have these general comments:

- please avoid using icons for phones or paperclips etc 
- use dummy text (one design used text from another website) 
- there won't any live social media feeds to the site
the client likes a lot of the designs that this company comes up with: 

i look forward to see some more designs

hi all, 

further to my last update, here are a few more pointers:
- there will be no search facilities - so no "search" box please 
- please just use the images supplied - no stock ones
- use just the page names give (no other pages) 

The client is looking for a simple, elegant design. 

Many thanks 
Rolf 

thanks for all the designs. 

I have uploaded another file to the brief which shows some posters that the client particularly likes. Perhaps the homepage could consist of large rectangle made up of a number of boxes - for some introductory text, a large image, mailing list, contact details, Lunch Special etc - just an idea! 
It's clear that the client likes clean lines with square edges. 
I want to be able to pass the designs directly onto the client so can designers avoid adding extra info or page. For example one design has a tab for a "Gift Card" - it will be easier for me if such additions are avoided. 

thanks!                                                                                                                                                                                                                                                                                                                                                                                                    

Thank you for all your designs - please keep them coming! 

hi all,

I am meeting the client tomorrow afternoon so please submit revisions / designs before then. 

Many thanks, 
Rolf

Target Market(s)

Business people, upmarket etc

Industry/Entity Type

Business

Requirements
Must have
• - The home page needs a slide show of images as well as:
- a mailing list form - very simple, "Join our mailing list - name, email"
- 3 or 4 sentences of text
- Friendloop link

```html
<!DOCTYPE html>
<html lang="en">
<head>
<meta charset="utf-8">
<title>Maplehaven Italian – Gallery</title>
<link rel="stylesheet" href="https://fonts.googleapis.com/css2?family=Crimson+Text:ital,wght@0,400;0,600;1,400&family=Arimo:wght@400&display=swap">
<style>
  :root {
    --sidebar-bg: #1e1e1e;
    --panel-bg: #262626;
    --rule: #3a3a3a;
    --gold: #b8953e;
    --gold-light: #d4b266;
    --text: #ffffff;
    --muted: #8a8a8a;
    --input-bg: #333333;
  }
  * { margin: 0; padding: 0; box-sizing: border-box; }
  html, body { width: 1200px; height: 750px; overflow: hidden; background: var(--sidebar-bg); }
  .page { position: relative; width: 1200px; height: 750px; overflow: hidden; font-family: "Arimo", Arial, sans-serif; color: var(--text); }

  /* sidebar */
  .sidebar { position: absolute; left: 0; top: 0; width: 357px; height: 750px; background: var(--sidebar-bg); }
  .sidebar .rule { position: absolute; left: 34px; width: 273px; height: 2px; background: var(--rule); }
  .brand { position: absolute; left: 34px; top: 30px; width: 273px; text-align: center; font-family: "Crimson Text", Georgia, serif; }
  .brand-name { font-size: 36px; font-weight: 400; letter-spacing: 1px; line-height: 40px; color: var(--text); }
  .brand-sub { font-size: 12px; letter-spacing: 4px; margin-left: 50px; color: var(--text); }

  .nav { position: absolute; left: 34px; top: 110px; width: 273px; list-style: none; }
  .nav li { height: 39px; border-bottom: 1px solid var(--rule); display: flex; align-items: center; padding-left: 18px; font-family: "Crimson Text", Georgia, serif; font-size: 15px; }
  .nav li:last-child { border-bottom: none; }
  .nav li svg { margin-right: 9px; }
  .nav li.current { color: var(--gold-light); }

  .newsletter-label { position: absolute; left: 41px; top: 390px; font-family: "Crimson Text", Georgia, serif; font-style: italic; font-size: 16px; color: var(--gold-light); }
  .newsletter-input { position: absolute; left: 40px; top: 417px; width: 200px; height: 35px; border-radius: 10px; background: var(--input-bg); color: var(--muted); font-size: 9px; padding-left: 13px; line-height: 35px; }
  .newsletter-submit { position: absolute; left: 253px; top: 423px; font-family: "Crimson Text", Georgia, serif; font-style: italic; font-size: 15px; text-decoration: underline; color: var(--text); }

  .promotions { position: absolute; left: 33px; top: 469px; width: 274px; height: 155px; border: 2px solid #3c3c3c; text-align: center; }
  .promotions h2 { font-family: "Crimson Text", Georgia, serif; font-style: italic; font-weight: 400; font-size: 20px; color: var(--gold-light); margin-top: 4px; }
  .promotions p { text-align: left; font-size: 8.5px; line-height: 15px; padding: 0 12px 0 25px; margin-top: 4px; }
  .promotions p + p { margin-top: 15px; }
  .btn-more { position: absolute; left: 86px; top: 117px; width: 87px; height: 25px; border-radius: 13px; background: linear-gradient(#d2b062, #a9873a); font-family: "Crimson Text", Georgia, serif; font-size: 12px; line-height: 25px; }

  .follow { position: absolute; left: 54px; top: 634px; display: flex; align-items: center; font-family: "Crimson Text", Georgia, serif; font-size: 14px; }
  .follow .label { font-style: italic; margin-right: 12px; }
  .follow .social { color: var(--gold); font-size: 15px; }
  .follow .divider { width: 1px; height: 14px; background: #555; margin: 0 9px; }

  /* gallery panel */
  .content { position: absolute; left: 357px; top: 0; width: 367px; height: 750px; background: linear-gradient(180deg, #262626 0%, #2c2b2a 50%, #2a2927 100%); }
  .content .gold-rule { position: absolute; left: 0; width: 367px; height: 2px; background: var(--gold); }
  .content h1 { position: absolute; top: 42px; width: 100%; text-align: center; font-family: "Crimson Text", Georgia, serif; font-weight: 400; font-size: 32px; }
  .intro { position: absolute; left: 18px; top: 127px; width: 335px; font-size: 8.5px; line-height: 15px; }
  .thumb { position: absolute; width: 85px; height: 85px; border-radius: 7px; }
  .t-pan { background: linear-gradient(135deg, #3a3a3a, #8c8470 55%, #2b2b2b); }
  .t-dish { background: linear-gradient(135deg, #7a5030, #c07a3a 50%, #4a2e1c); }
  .t-couple { background: linear-gradient(135deg, #5a4636, #d8bc92 55%, #2c2622); }
  .t-diners { background: linear-gradient(135deg, #3a2c24, #a28466 55%, #cfc5b5); }
  .t-sign { background: linear-gradient(135deg, #5a1e12, #b8642a 50%, #3a1a10); }
  .t-plate { background: linear-gradient(135deg, #d8b04a, #e0902a 55%, #7a5020); }

  /* interior image */
  .interior { position: absolute; left: 724px; top: 0; width: 476px; height: 750px; background: linear-gradient(160deg, #3a3a40 0%, #5a4a48 30%, #7a4a32 55%, #4a2416 80%, #2a140c 100%); }
  .reserve { position: absolute; left: 894px; top: -56px; width: 118px; height: 118px; border-radius: 50%; background: radial-gradient(circle at 50% 40%, #bdbdbd, #8e8e8e); text-align: center; font-family: "Crimson Text", Georgia, serif; font-style: italic; font-size: 17px; line-height: 14px; padding-top: 66px; }
</style>
</head>
<body>
<div class="page">

  <aside class="sidebar">
    <div class="rule" style="top:18px"></div>
    <div class="brand">
      <div class="brand-name">MAPLEHAVEN</div>
      <div class="brand-sub">ITALIAN</div>
    </div>
    <div class="rule" style="top:109px"></div>

    <ul class="nav">
      <li><svg width="14" height="8" viewBox="0 0 14 8"><path d="M0 4h12M9 1l3 3-3 3" stroke="#8a8a8a" fill="none"/></svg>Home</li>
      <li><svg width="14" height="8" viewBox="0 0 14 8"><path d="M0 4h12M9 1l3 3-3 3" stroke="#8a8a8a" fill="none"/></svg>Our Restaurant</li>
      <li><svg width="14" height="8" viewBox="0 0 14 8"><path d="M0 4h12M9 1l3 3-3 3" stroke="#8a8a8a" fill="none"/></svg>Our Menu</li>
      <li class="current"><svg width="14" height="8" viewBox="0 0 14 8"><path d="M0 4h12M9 1l3 3-3 3" stroke="#8a8a8a" fill="none"/></svg>Gallery</li>
      <li><svg width="14" height="8" viewBox="0 0 14 8"><path d="M0 4h12M9 1l3 3-3 3" stroke="#8a8a8a" fill="none"/></svg>Events</li>
      <li><svg width="14" height="8" viewBox="0 0 14 8"><path d="M0 4h12M9 1l3 3-3 3" stroke="#8a8a8a" fill="none"/></svg>Reservations</li>
      <li><svg width="14" height="8" viewBox="0 0 14 8"><path d="M0 4h12M9 1l3 3-3 3" stroke="#8a8a8a" fill="none"/></svg>Contact Us</li>
    </ul>
    <div class="rule" style="top:380px"></div>

    <div class="newsletter-label">Newsletter</div>
    <div class="newsletter-input">Enter you email</div>
    <div class="newsletter-submit">Submit</div>

    <section class="promotions">
      <h2>Our Promotions</h2>
      <p>But I must explain to you how all this mistaken idea of denouncing pleasure and praising pain was born</p>
      <p>and expound the actual teachings of the great explorer of the truth, the master-builder of human happiness.</p>
      <div class="btn-more">Read More</div>
    </section>

    <div class="follow">
      <span class="label">Follow us:</span>
      <span class="social">Friendloop</span>
      <span class="divider"></span>
      <span class="social">Chirpline</span>
    </div>
  </aside>

  <main class="content">
    <div class="gold-rule" style="top:17px"></div>
    <h1>Gallery</h1>
    <div class="gold-rule" style="top:109px"></div>
    <p class="intro">There are many variations of passages of Lorem Ipsum available, but the majority have suffered alteration in some form, by injected humour, or randomised words which don't look even slightly believable. If you are going to use a passage of Lorem Ipsum</p>

    <div class="thumb t-pan" style="left:29px;top:206px" role="img" aria-label="Pan flambéing on the stove"></div>
    <div class="thumb t-dish" style="left:144px;top:206px" role="img" aria-label="Grilled dish on a wooden board"></div>
    <div class="thumb t-couple" style="left:257px;top:206px" role="img" aria-label="Couple toasting with white wine"></div>

    <div class="thumb t-diners" style="left:29px;top:313px" role="img" aria-label="Guests dining at a table"></div>
    <div class="thumb t-sign" style="left:144px;top:313px" role="img" aria-label="Illuminated restaurant sign"></div>
    <div class="thumb t-plate" style="left:257px;top:313px" role="img" aria-label="Fried fish with lemon and chips"></div>

    <div class="thumb t-sign" style="left:29px;top:422px" role="img" aria-label="Illuminated restaurant sign"></div>
    <div class="thumb t-pan" style="left:144px;top:422px" role="img" aria-label="Pan flambéing on the stove"></div>
    <div class="thumb t-dish" style="left:257px;top:422px" role="img" aria-label="Grilled dish on a wooden board"></div>

    <div class="thumb t-plate" style="left:29px;top:537px" role="img" aria-label="Fried fish with lemon and chips"></div>
    <div class="thumb t-couple" style="left:144px;top:528px" role="img" aria-label="Couple toasting with white wine"></div>
    <div class="thumb t-diners" style="left:257px;top:528px" role="img" aria-label="Guests dining at a table"></div>
  </main>

  <div class="interior" role="img" aria-label="Restaurant lounge with leather sofas, candles and tall windows"></div>
  <div class="reserve">Reservation<br>Online</div>

</div>
</body>
</html>
```